Weightloss company needs Business Card

We want a business card that is clean and professional, yet portrays that we are a friendly, innovative, and versatile program designed to fit the needs of our clients.
I would like there to be 2 sides, one side having an appointment card, and the other side containing the logo and business information. There can be decorations on both sides. The logo is attached.

Target Market(s)

Men and women 40-60

Industry/Entity Type

Business

Contact Information for Business Card

Font styles to use
Sans Serif

Requirements
Must have
• The logo, space for business information
Nice to have
• The colors in the logo
Should not have
• No pictures of people or food

```html
<!DOCTYPE html>
<html lang="en">
<head>
<meta charset="utf-8">
<title>Pivotal Weight Co. — Business Card</title>
<link rel="stylesheet" href="https://fonts.googleapis.com/css2?family=Open+Sans:ital,wght@0,400;0,600;0,700;1,400&display=swap">
<style>
  :root {
    --brand-red: #d7153a;
    --brand-cyan: #2bb3de;
    --ink: #3e3e3e;
    --ink-soft: #555555;
    --card: #f4f4f4;
    --backdrop: #e4e4e6;
  }
  * { box-sizing: border-box; margin: 0; padding: 0; }
  html, body {
    width: 1105px; height: 1200px; overflow: hidden;
    background: var(--backdrop);
    font-family: "Open Sans", Arial, sans-serif;
    color: var(--ink);
  }
  .card {
    position: absolute; left: 182px; width: 746px; height: 424px;
    background: var(--card);
    overflow: hidden;
  }
  .card--front { top: 119px; }
  .card--back  { top: 637px; }

  /* Front */
  .brand {
    position: absolute; right: 40px; top: 72px;
    display: flex; align-items: center; gap: 12px;
  }
  .brand__name {
    font-size: 30px; font-weight: 700; color: var(--brand-red);
    letter-spacing: -0.3px;
  }
  .brand__dot {
    width: 18px; height: 18px; border-radius: 50%; background: var(--brand-red);
  }
  .person__name {
    position: absolute; left: 36px; top: 203px;
    font-size: 25px; font-weight: 600; color: var(--brand-red); letter-spacing: 0.3px;
  }
  .person__title {
    position: absolute; left: 36px; top: 240px;
    font-size: 18px; color: var(--brand-cyan);
  }
  .title-rule {
    position: absolute; left: 187px; right: 40px; top: 256px;
    height: 2px; background: var(--brand-cyan);
  }
  .contact-list {
    position: absolute; left: 36px; top: 278px; list-style: none;
  }
  .contact-list li {
    display: flex; align-items: center; gap: 10px;
    height: 29px; font-size: 19px; color: var(--ink);
  }
  .contact-list svg { width: 20px; height: 20px; fill: var(--brand-red); flex: none; }
  .address {
    position: absolute; right: 40px; top: 306px; text-align: right;
    font-size: 19px; line-height: 29px; color: var(--ink-soft);
  }
  .address .web { letter-spacing: 3px; }
  .edge-band { position: absolute; left: 0; bottom: 0; width: 746px; height: 10px; }

  /* Back */
  .appt__heading {
    position: absolute; left: 0; right: 0; top: 42px; text-align: center;
    font-size: 27px; font-weight: 600; color: var(--brand-red);
  }
  .appt__row { position: absolute; display: flex; align-items: baseline; }
  .appt__row--client { left: 50px; top: 117px; }
  .appt__row--when { left: 41px; top: 195px; }
  .dots { display: inline-block; border-bottom: 2px dotted #777; height: 1px; }
  .appt__label { font-size: 20px; color: var(--brand-red); }
  .appt__text { font-size: 19px; color: var(--ink-soft); margin-left: 10px; }
  .appt__ampm { font-size: 15px; color: var(--brand-red); margin-left: 4px; }
  .days { position: absolute; left: 0; top: 275px; width: 100%; height: 30px; }
  .day {
    position: absolute; display: flex; align-items: center; gap: 6px;
    font-size: 19px; color: var(--brand-red);
  }
  .day__box { width: 21px; height: 19px; border: 1.5px solid #555; }
  .notice {
    position: absolute; left: 0; right: 0; top: 356px; text-align: center;
    font-size: 15px; font-style: italic; line-height: 21px; color: var(--ink-soft);
  }
</style>
</head>
<body>

<section class="card card--front">
  <div class="brand">
    <span class="brand__name">Pivotal Weight Co.</span>
    <span class="brand__dot"></span>
  </div>

  <h1 class="person__name">DANIEL REYES</h1>
  <p class="person__title">CEO/FOUNDER</p>
  <div class="title-rule"></div>

  <ul class="contact-list">
    <li><svg viewBox="0 0 24 24"><path d="M6.6 10.8a15.1 15.1 0 0 0 6.6 6.6l2.2-2.2a1 1 0 0 1 1-.25 11.4 11.4 0 0 0 3.6.57 1 1 0 0 1 1 1V20a1 1 0 0 1-1 1A17 17 0 0 1 3 4a1 1 0 0 1 1-1h3.5a1 1 0 0 1 1 1c0 1.25.2 2.45.57 3.6a1 1 0 0 1-.25 1z"/></svg>555 210 4471</li>
    <li><svg viewBox="0 0 24 24"><path d="M7 2h10a2 2 0 0 1 2 2v16a2 2 0 0 1-2 2H7a2 2 0 0 1-2-2V4a2 2 0 0 1 2-2zm0 3v13h10V5zm5 14.2a1 1 0 1 0 0 .1z"/></svg>555 318 6625</li>
    <li><svg viewBox="0 0 24 24"><path d="M6 3h10l2 2v4H6zM3 10h18a1 1 0 0 1 1 1v7h-4v3H6v-3H2v-7a1 1 0 0 1 1-1zm5 6v3h8v-3z"/></svg>555 742 0893</li>
    <li><svg viewBox="0 0 24 24"><path d="M3 6h18v12H3zm2 1.5v.4l7 5 7-5v-.4z"/></svg>hello@pivotalweight.co</li>
  </ul>

  <address class="address" style="font-style:normal">
    1420 Birchwood Way<br>
    Cedar Falls, Oregon 97310<br>
    <span class="web">www.pivotalweight.co</span>
  </address>

  <svg class="edge-band" viewBox="0 0 746 10" preserveAspectRatio="none" aria-hidden="true">
    <polygon points="0,0 496,0 489,10 0,10" fill="var(--brand-red)"/>
    <polygon points="500,0 746,0 746,10 493,10" fill="var(--brand-cyan)"/>
  </svg>
</section>

<section class="card card--back">
  <h2 class="appt__heading">Next Appointment</h2>

  <div class="appt__row appt__row--client">
    <span class="dots" style="width:432px"></span>
    <span class="appt__text">has an appointment</span>
  </div>

  <div class="appt__row appt__row--when">
    <span class="appt__label">Date :</span>
    <span class="dots" style="width:280px;margin-left:14px"></span>
    <span class="appt__label" style="margin-left:25px">Time :</span>
    <span class="dots" style="width:146px;margin-left:6px"></span>
    <span class="appt__ampm">AM/PM</span>
  </div>

  <div class="days">
    <span class="day" style="left:47px">Sun <span class="day__box"></span></span>
    <span class="day" style="left:142px">Mon <span class="day__box"></span></span>
    <span class="day" style="left:243px">Tue <span class="day__box"></span></span>
    <span class="day" style="left:351px">Wed<span class="day__box"></span></span>
    <span class="day" style="left:452px">Thu<span class="day__box"></span></span>
    <span class="day" style="left:555px">Fri<span class="day__box"></span></span>
    <span class="day" style="left:634px">Sat <span class="day__box"></span></span>
  </div>

  <p class="notice">
    Please give me 24 hours notice if you are unable to keep your appointment or<br>
    a cancellation fee may be charged.
  </p>
</section>

</body>
</html>
```